FieldNest.com FACELIFT design for the online store

A) GENERAL
We need a small FACELIFT design with a short styleguide for our online store http://FieldNest.com (online store for sport goods; the store is just now in responsive design; actually only in German). The store is the first online store worldwide with 3d images for all products.
B) Designers: PLEASE NOTE:
- We don't want change functionality!
- We only want a small facelift.
- We don't need a fully coded website.
C) We only need for the responsive design views:
1. the home page design (one page)
http://www.fieldnest.com/de/
2. the category listing design (one page)
http://www.fieldnest.com/de/alle/running.html
3. the product detail page (one page)
http://www.fieldnest.com/de/varnok-tz-max-3d-qrt-herren-traillaufschuhe-dura-flex.html
4. the cms page (textonly !!!)
http://www.fieldnest.com/de/versand-und-lieferung
5. the Mega drop down
D) We intend to change/use:
- maybe to use a background image in the start page, and each category
- change the header
- change the font sizes for the titles (maybe in capital letters)
- change the mega drop down

```html
<!DOCTYPE html>
<html lang="en">
<head>
<meta charset="utf-8">
<title>FieldNest.com – Sports Categories Menu</title>
<link href="https://fonts.googleapis.com/css2?family=Roboto:wght@400;500;700&display=swap" rel="stylesheet">
<style>
:root{
  --ink:#111111;
  --muted:#8a8a8a;
  --accent:#e8401c;
  --nav-bg:#000000;
  --panel:#f4f4f4;
  --footer:#e6e6e6;
  --rule:#d9d9d9;
  --white:#ffffff;
}
*{box-sizing:border-box;margin:0;padding:0}
html,body{width:1200px;height:3492px;overflow:hidden;background:var(--white);font-family:'Roboto',Arial,sans-serif;color:var(--ink)}
.canvas{position:relative;width:1200px;height:3492px}
.row{position:absolute;left:0;width:1200px;transform:translateY(-50%);display:block}
.label{position:absolute;left:64px;top:50%;transform:translateY(-50%);font-size:34px;font-weight:500;letter-spacing:.5px;white-space:nowrap}
.sub .label{left:68px;font-weight:400;color:var(--muted);font-size:33px;letter-spacing:.3px}
.red .label{color:var(--accent);font-weight:500}
.icon{position:absolute;left:550px;top:50%;transform:translateY(-50%);width:46px;height:46px}
.sub .icon{left:558px;width:30px;height:30px}

.topbar{position:absolute;top:0;left:0;width:1200px;height:104px;background:var(--white)}
.topbar .title{position:absolute;left:56px;top:52px;transform:translateY(-50%);font-size:35px;font-weight:500}
.topbar .arrow{position:absolute;right:56px;top:32px;width:40px;height:40px}

.mainnav{position:absolute;top:104px;left:0;width:1200px;height:88px;background:var(--nav-bg)}
.mainnav .home{position:absolute;left:32px;top:0;width:88px;height:88px;background:var(--white)}
.mainnav .home svg{position:absolute;left:20px;top:16px;width:48px;height:48px}
.mainnav .link{position:absolute;top:44px;transform:translateY(-50%);color:var(--white);font-size:38px;font-weight:500;white-space:nowrap}

.panel{position:absolute;top:192px;left:0;width:1200px;height:1480px;background:var(--panel)}
.rule{position:absolute;left:0;width:1200px;height:3px;background:var(--rule)}

.locale{position:absolute;top:1672px;left:0;width:1200px;height:196px;background:var(--footer)}
.locale .country{position:absolute;left:72px;top:48px;transform:translateY(-50%);display:flex;align-items:center;gap:12px;font-size:31px;color:var(--muted)}
.locale .flag{width:52px;height:32px;display:block}
.locale .signin{position:absolute;left:74px;top:140px;transform:translateY(-50%);font-size:31px;color:var(--muted)}
.spacer{position:absolute;top:1868px;left:0;width:1200px;height:152px;background:var(--panel)}
</style>
</head>
<body>
<div class="canvas">

  <header class="topbar">
    <span class="title">SPORTS CATEGORIES</span>
    <svg class="arrow" viewBox="0 0 40 40"><path d="M12 4 L28 20 L12 36" fill="none" stroke="#111" stroke-width="5"/></svg>
  </header>

  <nav class="mainnav">
    <div class="home">
      <svg viewBox="0 0 48 48"><path d="M24 4 L2 24 H9 V44 H20 V31 H28 V44 H39 V24 H46 Z" fill="#111"/></svg>
    </div>
    <span class="link" style="left:152px">MEN</span>
    <span class="link" style="left:276px">WOMEN</span>
    <span class="link" style="left:464px">CHILDREN/YOUTH</span>
    <span class="link" style="left:816px">GIFT IDEAS</span>
  </nav>

  <section class="panel"></section>

  <div class="row" style="top:248px"><span class="label">OUTDOOR</span>
    <svg class="icon" viewBox="0 0 46 46"><circle cx="23" cy="23" r="20" fill="none" stroke="#111" stroke-width="3"/><line x1="13" y1="23" x2="33" y2="23" stroke="#111" stroke-width="3"/></svg></div>

  <div class="row sub" style="top:324px"><span class="label">Outdoor Clothing</span><svg class="icon" viewBox="0 0 30 30"><path d="M9 3 L21 15 L9 27" fill="none" stroke="#333" stroke-width="3"/></svg></div>
  <div class="row sub" style="top:400px"><span class="label">Shoes &amp; Sticks</span><svg class="icon" viewBox="0 0 30 30"><path d="M9 3 L21 15 L9 27" fill="none" stroke="#333" stroke-width="3"/></svg></div>
  <div class="row sub" style="top:472px"><span class="label">Backpacks &amp; Headlamps</span><svg class="icon" viewBox="0 0 30 30"><path d="M9 3 L21 15 L9 27" fill="none" stroke="#333" stroke-width="3"/></svg></div>
  <div class="row sub" style="top:548px"><span class="label">Tents</span><svg class="icon" viewBox="0 0 30 30"><path d="M9 3 L21 15 L9 27" fill="none" stroke="#333" stroke-width="3"/></svg></div>
  <div class="row sub" style="top:624px"><span class="label">Camping</span><svg class="icon" viewBox="0 0 30 30"><path d="M9 3 L21 15 L9 27" fill="none" stroke="#333" stroke-width="3"/></svg></div>
  <div class="row sub" style="top:696px"><span class="label">Winter Hiking</span><svg class="icon" viewBox="0 0 30 30"><path d="M9 3 L21 15 L9 27" fill="none" stroke="#333" stroke-width="3"/></svg></div>

  <div class="rule" style="top:743px"></div>
  <div class="row" style="top:788px"><span class="label">ROCK CLIMBING</span><svg class="icon" viewBox="0 0 46 46"><circle cx="23" cy="23" r="20" fill="none" stroke="#111" stroke-width="3"/><path d="M13 23 H33 M23 13 V33" stroke="#111" stroke-width="3"/></svg></div>
  <div class="rule" style="top:831px"></div>
  <div class="row" style="top:876px"><span class="label">RUNNING</span><svg class="icon" viewBox="0 0 46 46"><circle cx="23" cy="23" r="20" fill="none" stroke="#111" stroke-width="3"/><path d="M13 23 H33 M23 13 V33" stroke="#111" stroke-width="3"/></svg></div>
  <div class="rule" style="top:920px"></div>
  <div class="row" style="top:964px"><span class="label">BIKE</span><svg class="icon" viewBox="0 0 46 46"><circle cx="23" cy="23" r="20" fill="none" stroke="#111" stroke-width="3"/><path d="M13 23 H33 M23 13 V33" stroke="#111" stroke-width="3"/></svg></div>
  <div class="rule" style="top:1010px"></div>
  <div class="row" style="top:1056px"><span class="label">SKI &amp; FREERIDE</span><svg class="icon" viewBox="0 0 46 46"><circle cx="23" cy="23" r="20" fill="none" stroke="#111" stroke-width="3"/><path d="M13 23 H33 M23 13 V33" stroke="#111" stroke-width="3"/></svg></div>
  <div class="rule" style="top:1100px"></div>
  <div class="row" style="top:1144px"><span class="label">SKI TOURING</span><svg class="icon" viewBox="0 0 46 46"><circle cx="23" cy="23" r="20" fill="none" stroke="#111" stroke-width="3"/><path d="M13 23 H33 M23 13 V33" stroke="#111" stroke-width="3"/></svg></div>
  <div class="rule" style="top:1188px"></div>
  <div class="row" style="top:1236px"><span class="label">FITNESS</span><svg class="icon" viewBox="0 0 46 46"><circle cx="23" cy="23" r="20" fill="none" stroke="#111" stroke-width="3"/><path d="M13 23 H33 M23 13 V33" stroke="#111" stroke-width="3"/></svg></div>
  <div class="rule" style="top:1278px"></div>
  <div class="row" style="top:1324px"><span class="label">FASHION</span><svg class="icon" viewBox="0 0 46 46"><circle cx="23" cy="23" r="20" fill="none" stroke="#111" stroke-width="3"/><path d="M13 23 H33 M23 13 V33" stroke="#111" stroke-width="3"/></svg></div>
  <div class="rule" style="top:1366px"></div>
  <div class="row" style="top:1416px"><span class="label">DIGITAL</span><svg class="icon" viewBox="0 0 46 46"><circle cx="23" cy="23" r="20" fill="none" stroke="#111" stroke-width="3"/><path d="M13 23 H33 M23 13 V33" stroke="#111" stroke-width="3"/></svg></div>
  <div class="rule" style="top:1456px"></div>

  <div class="row red" style="top:1508px"><span class="label">REMAINING STOCK</span></div>
  <div class="row red" style="top:1596px"><span class="label">DEALS</span></div>

  <footer class="locale">
    <div class="country">
      <svg class="flag" viewBox="0 0 52 32"><rect width="52" height="11" y="0" fill="#000"/><rect width="52" height="11" y="10.5" fill="#dd0000"/><rect width="52" height="11" y="21" fill="#ffce00"/></svg>
      <span>GERMANY</span>
      <svg width="26" height="20" viewBox="0 0 26 20"><path d="M3 5 L13 15 L23 5" fill="none" stroke="#666" stroke-width="3.5"/></svg>
    </div>
    <span class="signin">SIGN IN</span>
  </footer>
  <div class="spacer"></div>

</div>
</body>
</html>
```